Corvelle Meadow Organic Flower Farm, Farmer Florist

I am a flower grower and florist, so I do everything from the field to the vase. I want to include my website, phone, email and instagram

```html
<!DOCTYPE html>
<html lang="en">
<head>
<meta charset="utf-8">
<title>Corvelle Meadow – Business Cards</title>
<link rel="stylesheet" href="https://fonts.googleapis.com/css2?family=Cinzel:wght@400;600&family=Arimo:wght@400&display=swap">
<style>
  :root{
    --backdrop:#141414;
    --card:#2a2a2b;
    --card-shade:#232324;
    --rose:#e58a85;
    --wine:#6e2d2e;
    --rule:#3b3b3c;
  }
  *{margin:0;padding:0;box-sizing:border-box}
  html,body{width:1200px;height:820px;overflow:hidden;background:var(--backdrop)}
  .stage{position:relative;width:1200px;height:820px}
  .card{
    position:absolute;width:540px;height:310px;
    background:linear-gradient(135deg,var(--card),var(--card-shade));
    border-bottom:3px solid var(--rose);
    border-left:2px solid var(--rose);
    box-shadow:0 18px 40px rgba(0,0,0,.6);
  }
  .card--front{left:45px;top:255px}
  .card--back{left:615px;top:255px}

  .brand{position:absolute;text-align:center}
  .card--front .brand{left:250px;top:70px;width:250px}
  .brand__dot{display:block;width:34px;height:34px;border-radius:50%;background:var(--rose);margin:0 auto 14px}
  .brand__name{font-family:"Cinzel",serif;font-weight:400;color:var(--wine);letter-spacing:.12em;font-size:34px;line-height:1}
  .card--back .brand{left:0;top:125px;width:540px}
  .card--back .brand__name{font-size:44px}

  .divider{position:absolute;left:190px;top:178px;width:300px;height:1px;background:var(--rule)}

  .person{position:absolute;left:40px;top:165px}
  .person__name{font-family:"Cinzel",serif;font-weight:600;color:var(--rose);font-size:21px;letter-spacing:.03em}
  .person__role{font-family:"Arimo",sans-serif;color:var(--wine);font-size:14px;margin-top:2px}

  .contact{position:absolute;left:40px;top:228px;list-style:none}
  .contact li{display:flex;align-items:center;gap:9px;font-family:"Arimo",sans-serif;font-size:14px;color:var(--wine);height:21px}
  .contact svg{width:15px;height:15px;flex:none}

  .social{position:absolute;right:30px;top:236px;display:flex;align-items:center;gap:8px;font-family:"Arimo",sans-serif;font-size:14px;color:var(--wine)}
  .social__mark{width:14px;height:14px;border:2px solid var(--rose);border-radius:50%}
</style>
</head>
<body>
<main class="stage">

  <section class="card card--front" aria-label="Business card front">
    <div class="brand">
      <span class="brand__dot"></span>
      <div class="brand__name">CORVELLE</div>
    </div>
    <div class="divider"></div>

    <div class="person">
      <div class="person__name">ELIAS MARLOW</div>
      <div class="person__role">Managing Director</div>
    </div>

    <ul class="contact">
      <li>
        <svg viewBox="0 0 16 16" fill="none" stroke="var(--rose)" stroke-width="1.6"><path d="M3 2h3l1.5 3.5-2 1.3a8 8 0 0 0 3.7 3.7l1.3-2L14 10v3a1 1 0 0 1-1 1A11 11 0 0 1 2 3a1 1 0 0 1 1-1z"/></svg>
        044-555 018 273
      </li>
      <li>
        <svg viewBox="0 0 16 16" fill="var(--rose)"><path d="M1 3h14v10H1z"/><path d="M1 3l7 6 7-6" fill="none" stroke="var(--card)" stroke-width="1.4"/></svg>
        info@corvellemeadow.com
      </li>
      <li>
        <svg viewBox="0 0 16 16" fill="none" stroke="var(--rose)" stroke-width="1.4"><circle cx="8" cy="8" r="6.5"/><ellipse cx="8" cy="8" rx="3" ry="6.5"/><path d="M1.5 8h13M2.5 5h11M2.5 11h11"/></svg>
        www.corvellemeadow.com
      </li>
    </ul>

    <div class="social">
      <span>@corvellemeadow</span>
      <span class="social__mark"></span>
    </div>
  </section>

  <section class="card card--back" aria-label="Business card back">
    <div class="brand">
      <div class="brand__name">CORVELLE</div>
    </div>
  </section>

</main>
</body>
</html>
```